Local fast-growing company in the service sector

We are looking for a modern business card design, which should also appear on our letterheads

Target Market(s)

Private and industrial sectors

Contact Information for Business Card

Vorname Name
Kellberger Str. 18
72418 Kellbach
Tel.: 07146-839214-0
Name@agentur-kvtl.de

Colors
9d9d9d
919191
aaaaaa

Requirements
Must have
• The logo (file) in silver

```html
<!DOCTYPE html>
<html lang="de">
<head>
<meta charset="utf-8">
<title>KVTL Visitenkarte</title>
<link rel="stylesheet" href="https://fonts.googleapis.com/css2?family=Source+Sans+3:wght@400;600&display=swap">
<style>
  :root {
    --stage: #000000;
    --card-front: #5f5f5f;
    --card-back: #646464;
    --silver: #b9b9b9;
    --silver-dark: #9d9d9d;
    --text-light: #ececec;
    --rule: #d8d8d8;
  }
  * { margin: 0; padding: 0; box-sizing: border-box; }
  html, body {
    width: 1200px; height: 900px; overflow: hidden;
    background: var(--stage);
    font-family: "Source Sans 3", "Myriad Pro", sans-serif;
  }
  .canvas { position: relative; width: 1200px; height: 900px; }

  .card {
    position: absolute; top: 275px; width: 477px; height: 293px;
  }
  .card-front {
    left: 116px; background: var(--card-front);
    border-radius: 0 46px 0 46px;
  }
  .card-back {
    left: 622px; background: var(--card-back);
    border-radius: 46px 0 46px 0;
  }
  .back-texture {
    position: absolute; inset: 0; border-radius: inherit;
    background: linear-gradient(180deg, #6a6a6a 0%, #606060 100%);
  }

  .brand {
    position: absolute; display: flex; align-items: center; gap: 14px;
    color: var(--silver);
  }
  .brand-mark {
    width: 44px; height: 44px; background: var(--silver-dark);
  }
  .brand-name {
    font-size: 54px; font-weight: 600; letter-spacing: 1px; line-height: 1;
  }
  .card-front .brand { right: 26px; top: 50px; }
  .card-back .brand { left: 124px; top: 107px; }

  .holder {
    position: absolute; left: 28px; top: 171px; width: 423px;
    display: flex; align-items: center; gap: 9px;
  }
  .holder-name {
    font-size: 18.5px; color: var(--text-light); white-space: nowrap; letter-spacing: 0.3px;
  }
  .holder-rule { flex: 1; height: 1.5px; background: var(--rule); }

  .contact-list {
    position: absolute; left: 26px; top: 209px; list-style: none;
    font-size: 14.5px; color: var(--text-light); line-height: 17.5px;
  }
  .contact-list li { display: flex; align-items: center; gap: 5px; }
  .contact-list svg { width: 12px; height: 12px; fill: var(--text-light); }

  .address {
    position: absolute; right: 26px; top: 227px; text-align: right;
    font-size: 14.5px; color: var(--text-light); line-height: 17.5px; font-style: normal;
  }
</style>
</head>
<body>
<main class="canvas">
  <section class="card card-front" aria-label="Vorderseite">
    <div class="brand">
      <span class="brand-mark"></span>
      <span class="brand-name">KVTL</span>
    </div>

    <div class="holder">
      <span class="holder-name">VORNAME NAME</span>
      <span class="holder-rule"></span>
    </div>

    <ul class="contact-list">
      <li>
        <svg viewBox="0 0 12 12" aria-hidden="true"><path d="M2.5 1l2 2.2-1 1.3a6.5 6.5 0 0 0 4 4l1.3-1 2.2 2-1.3 1.5C5.5 11 1 6.5 1 2.3z"/></svg>
        07146-839214-0
      </li>
      <li>
        <svg viewBox="0 0 12 12" aria-hidden="true"><path d="M1 3h10v6.5H1z M1.5 3.3L6 6.7l4.5-3.4" stroke="#5f5f5f" stroke-width="0.9"/></svg>
        Name@agentur-kvtl.de
      </li>
      <li>
        <svg viewBox="0 0 12 12" aria-hidden="true"><circle cx="6" cy="6" r="5"/><path d="M1 6h10M6 1c-2.5 3-2.5 7 0 10M6 1c2.5 3 2.5 7 0 10" stroke="#5f5f5f" stroke-width="0.8" fill="none"/></svg>
        www.agentur-kvtl.de
      </li>
    </ul>

    <address class="address">
      Kellberger Str. 18<br>
      72418 Kellbach
    </address>
  </section>

  <section class="card card-back" aria-label="Rückseite">
    <div class="back-texture" role="img" aria-label="Dezentes Wiederholungsmuster als Hintergrund"></div>
    <div class="brand">
      <span class="brand-mark"></span>
      <span class="brand-name">KVTL</span>
    </div>
  </section>
</main>
</body>
</html>
```